Tree Service Billboard 20x8 ft

We need a billboard design for a tree service company.
The billboard is 20ft x 8 ft so we need a design that is capable to stretching to those dimensions without loosing quality.
I have attached a series of images.
Image 1- Simply a billboard that I think looks good that I would like you to use for inspiration. I am aiming for the same format only no color in the wording, just black white, or gray. I like the the trees in the background, the logo placed to the left, and wording on the right.
Image 2- Current Logo I would like to the left of the billboard
Image 3- Another format of current logo if needed.
Image 4- A drawn out design template
Image 5- Another drawn out design template

Specific things I am looking for
-The contact number to be the largest thing on the design
-The logo on the design
-Key points to the design to say:
Tree Removal
Tree Trimming
Land Development
Stump Grinding
Storm Response
Insured
Free Bids
-The facebook logo
-The Google Logo

```html
<!DOCTYPE html>
<html lang="en">
<head>
<meta charset="utf-8">
<title>Birch Hollow Tree Service – Billboard</title>
<link rel="stylesheet" href="https://fonts.googleapis.com/css2?family=Anton&family=Bebas+Neue&family=Open+Sans:wght@600;700&display=swap">
<style>
  :root {
    --white: #ffffff;
    --phone-shade: #c9c9c9;
    --accent-gold: #d6a221;
    --forest-dark: #1d2a12;
    --forest-mid: #3f5a22;
    --forest-light: #7d8f33;
    --meadow: #4f7d28;
  }
  html, body {
    margin: 0;
    padding: 0;
    width: 1200px;
    height: 479px;
    overflow: hidden;
    background: var(--forest-dark);
  }
  .billboard {
    position: relative;
    width: 1200px;
    height: 479px;
    overflow: hidden;
    font-family: "Open Sans", sans-serif;
    color: var(--white);
  }
  .forest-backdrop {
    position: absolute;
    inset: 0;
    background:
      linear-gradient(180deg, rgba(0,0,0,0) 70%, rgba(0,0,0,0.25) 100%),
      linear-gradient(180deg, var(--forest-dark) 0%, var(--forest-mid) 35%, var(--forest-light) 55%, var(--forest-mid) 72%, var(--meadow) 82%, #3c6a1e 100%);
  }
  .brand-mark {
    position: absolute;
    left: 364px;
    top: 38px;
    width: 190px;
    height: 190px;
    border: 5px solid var(--white);
    border-radius: 50%;
    box-sizing: border-box;
  }
  .brand-name {
    position: absolute;
    left: 256px;
    top: 240px;
    width: 422px;
    margin: 0;
    text-align: center;
    font-family: "Bebas Neue", sans-serif;
    font-weight: 400;
    font-size: 50px;
    line-height: 60px;
    white-space: nowrap;
    color: var(--white);
  }
  .phone-number {
    position: absolute;
    left: 84px;
    top: 322px;
    width: 770px;
    margin: 0;
    text-align: center;
    font-family: "Anton", sans-serif;
    font-size: 128px;
    line-height: 130px;
    letter-spacing: 5px;
    white-space: nowrap;
    background: linear-gradient(180deg, var(--white) 60%, var(--phone-shade) 100%);
    -webkit-background-clip: text;
    background-clip: text;
    color: transparent;
  }
  .service-list {
    position: absolute;
    right: 40px;
    top: 44px;
    margin: 0;
    padding: 0;
    list-style: none;
  }
  .service-item {
    display: flex;
    justify-content: flex-end;
    align-items: center;
    height: 40.5px;
    font-weight: 700;
    font-size: 26px;
    white-space: nowrap;
  }
  .service-item::after {
    content: "";
    width: 17px;
    height: 19px;
    margin-left: 7px;
    background: var(--accent-gold);
  }
  .contact-links {
    position: absolute;
    left: 882px;
    top: 358px;
    margin: 0;
    padding: 0;
    list-style: none;
  }
  .contact-link {
    display: flex;
    align-items: center;
    height: 38px;
    font-weight: 600;
    font-size: 19px;
    white-space: nowrap;
  }
  .contact-icon {
    width: 31px;
    height: 31px;
    margin-right: 11px;
    flex: none;
  }
  .social-dot {
    width: 27px;
    height: 27px;
    margin: 0 13px 0 2px;
    border: 2.5px solid var(--white);
    border-radius: 50%;
    box-sizing: border-box;
    flex: none;
  }
</style>
</head>
<body>
  <main class="billboard">
    <div class="forest-backdrop" role="img" aria-label="Photograph of a sunlit orchard of green and autumn-tinged trees on a grassy meadow"></div>

    <div class="brand-mark" aria-hidden="true"></div>
    <h1 class="brand-name">Birch Hollow Tree Service</h1>

    <p class="phone-number">417-555-0148</p>

    <ul class="service-list">
      <li class="service-item">Tree Removal</li>
      <li class="service-item">Tree Trimming</li>
      <li class="service-item">Land Development</li>
      <li class="service-item">Stump Grinding</li>
      <li class="service-item">Storm Response</li>
      <li class="service-item">Insured</li>
      <li class="service-item">Free Bids</li>
    </ul>

    <ul class="contact-links">
      <li class="contact-link">
        <svg class="contact-icon" viewBox="0 0 32 32" aria-hidden="true" fill="none" stroke="#ffffff" stroke-width="2">
          <circle cx="16" cy="16" r="14"/>
          <ellipse cx="16" cy="16" rx="6" ry="14"/>
          <line x1="16" y1="2" x2="16" y2="30"/>
          <line x1="2" y1="16" x2="30" y2="16"/>
          <path d="M4.5 9h23M4.5 23h23"/>
        </svg>
        www.birchhollowtree.com
      </li>
      <li class="contact-link">
        <span class="social-dot" aria-hidden="true"></span>
        social.example/birchhollow
      </li>
    </ul>
  </main>
</body>
</html>
```